BOLD & MINIMALIST DESIGN NEEDED

We want a very bold but minimalistic business card design that is impactful and utilizes both sides of the business card. Our current logo is included for your use.

We want bold fonts and good use of negative space. We don't want the logo to overpower the design.

Target Market(s)

Professionals who are building new commercial buildings.

Industry/Entity Type

Construction

Contact Information for Business Card

Name, Title, email, office phone, cell phone, website

Font styles to use
Serif
Sans Serif

Requirements
Must have
• Bold design!

```html
<!DOCTYPE html>
<html lang="en">
<head>
<meta charset="utf-8">
<title>Ridgeline Design + Build – Business Card</title>
<link rel="stylesheet" href="https://fonts.googleapis.com/css2?family=Montserrat:wght@400;500;700;800&display=swap">
<style>
  :root {
    --backdrop: #9a9a9a;
    --card: #151515;
    --green: #86c440;
    --white: #ffffff;
    --soft-white: #f2f2f2;
  }
  * { margin: 0; padding: 0; box-sizing: border-box; }
  html, body {
    width: 1200px;
    height: 1108px;
    overflow: hidden;
    background: var(--backdrop);
    font-family: "Montserrat", sans-serif;
  }
  .card {
    position: absolute;
    left: 240px;
    width: 718px;
    height: 412px;
    background: var(--card);
    border-radius: 30px;
    border-left: 3px solid var(--green);
    border-bottom: 3px solid var(--green);
    overflow: hidden;
  }
  .card--front { top: 119px; }
  .card--back { top: 580px; }

  /* Front */
  .front-brand {
    position: absolute;
    left: 0; right: 0;
    top: 150px;
    text-align: center;
    color: var(--soft-white);
    font-weight: 800;
  }
  .front-brand__mark {
    display: block;
    width: 40px; height: 40px;
    margin: 0 auto 22px;
    background: var(--soft-white);
  }
  .front-brand__name {
    font-size: 64px;
    line-height: 1;
    letter-spacing: 1px;
  }
  .front-brand__tagline {
    font-size: 24px;
    letter-spacing: 17px;
    margin-top: 12px;
    padding-left: 17px;
  }

  /* Back */
  .back-brand {
    position: absolute;
    left: 0; right: 0;
    top: 48px;
    text-align: center;
    color: var(--white);
    font-weight: 800;
  }
  .back-brand__mark {
    display: block;
    width: 26px; height: 26px;
    margin: 0 auto 34px;
    background: var(--white);
  }
  .back-brand__name {
    font-size: 38px;
    line-height: 1;
  }
  .back-brand__tagline {
    font-size: 13px;
    letter-spacing: 7px;
    margin-top: 8px;
    padding-left: 7px;
  }

  .person {
    position: absolute;
    right: 389px;
    top: 240px;
    text-align: right;
  }
  .person__name {
    color: var(--green);
    font-weight: 700;
    font-size: 33px;
    line-height: 1;
    letter-spacing: 0.5px;
  }
  .person__title {
    color: var(--white);
    font-weight: 500;
    font-size: 18px;
    margin-top: 14px;
    letter-spacing: 0.5px;
  }
  .divider {
    position: absolute;
    left: 354px;
    top: 226px;
    width: 2px;
    height: 100px;
    background: var(--green);
  }
  .contacts {
    position: absolute;
    left: 393px;
    top: 217px;
    list-style: none;
  }
  .contacts__item {
    display: flex;
    align-items: center;
    height: 29px;
    color: var(--white);
    font-size: 19px;
    letter-spacing: 0.4px;
  }
  .contacts__icon {
    width: 15px; height: 15px;
    margin-right: 10px;
    flex: none;
  }
  .address-band {
    position: absolute;
    left: 0; right: 0;
    top: 358px;
    height: 25px;
    background: var(--green);
    color: var(--white);
    font-size: 17px;
    line-height: 25px;
    text-align: center;
    letter-spacing: 0.4px;
  }
</style>
</head>
<body>

<section class="card card--front" aria-label="Card front">
  <div class="front-brand">
    <span class="front-brand__mark"></span>
    <div class="front-brand__name">RIDGELINE</div>
    <div class="front-brand__tagline">DESIGN + BUILD</div>
  </div>
</section>

<section class="card card--back" aria-label="Card back">
  <div class="back-brand">
    <span class="back-brand__mark"></span>
    <div class="back-brand__name">RIDGELINE</div>
    <div class="back-brand__tagline">DESIGN + BUILD</div>
  </div>

  <div class="person">
    <div class="person__name">MARCUS DELANE</div>
    <div class="person__title">OWNER-CEO</div>
  </div>

  <div class="divider"></div>

  <ul class="contacts">
    <li class="contacts__item">
      <svg class="contacts__icon" viewBox="0 0 16 16" aria-hidden="true"><path fill="#86c440" d="M1 5c0-2 3-3 7-3s7 1 7 3v1h-4V4.5H5V6H1zM4 7h8l2 6H2z"/><circle cx="8" cy="10" r="1.6" fill="#151515"/></svg>
      123 456 789
    </li>
    <li class="contacts__item">
      <svg class="contacts__icon" viewBox="0 0 16 16" aria-hidden="true"><rect x="4" y="1" width="8" height="14" rx="1.5" fill="none" stroke="#86c440" stroke-width="1.6"/><circle cx="8" cy="12.5" r="0.9" fill="#86c440"/></svg>
      123 456 789
    </li>
    <li class="contacts__item">
      <svg class="contacts__icon" viewBox="0 0 16 16" aria-hidden="true"><rect x="1" y="3.5" width="14" height="9" fill="#86c440"/><path d="M1.5 4l6.5 5 6.5-5M1.5 12l4.5-4M14.5 12l-4.5-4" fill="none" stroke="#151515" stroke-width="1.1"/></svg>
      info@yourgmail.com
    </li>
    <li class="contacts__item">
      <svg class="contacts__icon" viewBox="0 0 16 16" aria-hidden="true"><circle cx="8" cy="8" r="7" fill="#86c440"/><path d="M4 4c2 0 2 2 4 2s0 3-2 3-1 3-3 2M10 10c1-1 3-1 3 1" fill="none" stroke="#151515" stroke-width="1.3"/></svg>
      www.yourwebsite.com
    </li>
  </ul>

  <div class="address-band">Your address, City State, Zip 1234</div>
</section>

</body>
</html>
```